Irrigation Business needs their business cards modernised and revamped

I would like to keep my current logo, colours and revamp the format of the card.

I would like the card to be clean yet important.

Im not sure if you include texture but i would like the named logo to be indented into the card etc.

show me something alive and free something thats clinical to the point yet has a feel of achievement. i would like people to go nice card.

Target Market(s)

high end clients, corporate, sports field manger, the guys that make the decisions

Industry/Entity Type

Business

Contact Information for Business Card

nformation to be included

Dean Harlow (Director)
0487305526
dean@kolvat.biz
www.kestonfieldworks.com

instagram logo
google logo
facebook logo

Colors

Designer to choose colors to be used in the design.

Requirements
Nice to have
• indentations a really nice feel to the card good texture

```html
<!DOCTYPE html>
<html lang="en">
<head>
<meta charset="utf-8">
<title>Kestonfield Works — Business Card</title>
<link rel="stylesheet" href="https://fonts.googleapis.com/css2?family=Open+Sans:wght@400;600;700&display=swap">
<style>
  :root {
    --backdrop: #2a2b2d;
    --card-white: #f7f7f5;
    --blue-light: #4ba8e0;
    --blue-mid: #3677bd;
    --blue-deep: #2f66ae;
    --brand-blue: #356fb8;
    --brand-green: #45b06a;
    --text-grey: #5d6168;
  }
  * { box-sizing: border-box; margin: 0; padding: 0; }
  html, body {
    width: 1200px; height: 840px; overflow: hidden;
    background: var(--backdrop);
    font-family: "Open Sans", Arial, sans-serif;
  }
  .canvas { position: relative; width: 1200px; height: 840px; }

  .card {
    position: absolute;
    width: 540px; height: 308px;
    border-radius: 3px;
    box-shadow: 0 10px 24px rgba(0,0,0,.35);
    overflow: hidden;
  }

  /* Back of card */
  .card-back {
    left: 60px; top: 110px;
    background: linear-gradient(100deg, var(--blue-light) 0%, var(--blue-mid) 55%, var(--blue-deep) 100%);
  }
  .card-back .brand {
    position: absolute; left: 0; right: 0; top: 40px;
    display: flex; flex-direction: column; align-items: center; gap: 10px;
  }
  .card-back .brand-mark {
    width: 150px; height: 150px; border-radius: 50%;
    background: var(--brand-green);
  }
  .card-back .brand-name {
    font-weight: 700; font-size: 17px; color: var(--brand-green);
    letter-spacing: .3px;
  }
  .social-row {
    position: absolute; top: 258px; left: 0; right: 0;
    display: flex; justify-content: center; gap: 7px;
    padding-left: 72px;
  }
  .social-row span {
    width: 17px; height: 17px; border-radius: 50%;
    background: var(--brand-green);
  }

  /* Front of card */
  .card-front {
    left: 600px; top: 420px;
    background: var(--card-white);
  }
  .card-front .brand {
    position: absolute; right: 26px; top: 18px;
    display: flex; flex-direction: column; align-items: center; gap: 10px;
  }
  .card-front .brand-mark {
    width: 210px; height: 210px; border-radius: 50%;
    background: var(--brand-blue);
  }
  .card-front .brand-name {
    font-weight: 700; font-size: 18px; color: var(--brand-blue);
  }
  .contact {
    position: absolute; left: 30px; bottom: 24px;
  }
  .contact .person {
    font-weight: 700; font-size: 15px; color: var(--brand-blue);
    text-transform: uppercase; line-height: 1.1;
  }
  .contact .role {
    font-weight: 400; font-size: 15px; color: var(--brand-green);
    text-transform: uppercase; line-height: 1.2; margin-bottom: 6px;
  }
  .contact ul { list-style: none; }
  .contact li {
    display: flex; align-items: center; gap: 8px;
    font-size: 14px; color: var(--text-grey); line-height: 1.35;
  }
  .contact svg { width: 11px; height: 11px; fill: var(--brand-blue); flex: none; }
</style>
</head>
<body>
<main class="canvas">

  <section class="card card-back" aria-label="Business card back">
    <div class="brand">
      <span class="brand-mark"></span>
      <span class="brand-name">Kestonfield Works</span>
    </div>
    <div class="social-row" aria-label="Social profiles">
      <span></span><span></span><span></span>
    </div>
  </section>

  <section class="card card-front" aria-label="Business card front">
    <div class="brand">
      <span class="brand-mark"></span>
      <span class="brand-name">Kestonfield Works</span>
    </div>
    <div class="contact">
      <p class="person">Dean Harlow</p>
      <p class="role">Director</p>
      <ul>
        <li>
          <svg viewBox="0 0 12 12" aria-hidden="true"><path d="M2.5 1l2 2.2-1 1.3c.7 1.5 1.6 2.4 3 3l1.3-1 2.2 2-1.2 1.8C4.8 10 2 7.2 1 3.2z"/></svg>
          0487305526
        </li>
        <li>
          <svg viewBox="0 0 12 12" aria-hidden="true"><path d="M1 3h10v6.5H1z M1.3 3.2L6 6.8l4.7-3.6" stroke="#f7f7f5" stroke-width=".8"/></svg>
          dean@kolvat.biz
        </li>
        <li>
          <svg viewBox="0 0 12 12" aria-hidden="true"><circle cx="6" cy="6" r="5"/><path d="M1 6h10M6 1c-2 2.8-2 7.2 0 10M6 1c2 2.8 2 7.2 0 10" stroke="#f7f7f5" stroke-width=".7" fill="none"/></svg>
          www.kestonfieldworks.com
        </li>
      </ul>
    </div>
  </section>

</main>
</body>
</html>
```